Hair salon Business Card

Beauty Salon
I would like to see designs using sky blue and a soft orange. Mainly I would like my name ( Gloss N' Wave Salon ) used as the design

Industry/Entity Type

Business

Contact Information for Business Card

Gloss N'Wave Salon
318 E Maple Hyw #14
Elm Ridge, Ca 91842
909 555-2716

```html
<!DOCTYPE html>
<html lang="en">
<head>
<meta charset="utf-8">
<title>Gloss N'Wave Salon – Business Cards</title>
<link rel="stylesheet" href="https://fonts.googleapis.com/css2?family=Questrial&family=Cinzel:wght@400&family=Open+Sans:wght@400;600&display=swap">
<style>
  :root {
    --salon-orange: #d17f0b;
    --salon-blue: #1a56b8;
    --card-white: #ffffff;
    --ink: #222222;
    --backdrop: #efece8;
  }
  * { margin: 0; padding: 0; box-sizing: border-box; }
  html, body { width: 1200px; height: 900px; overflow: hidden; }
  body { background: var(--backdrop); position: relative; }

  .card {
    position: absolute;
    border-radius: 14px;
    overflow: hidden;
    box-shadow: 0 6px 18px rgba(0,0,0,0.15);
  }
  .card-front { left: 78px; top: 35px; width: 588px; height: 363px; background: var(--card-white); }
  .card-back  { left: 389px; top: 506px; width: 566px; height: 350px; background: var(--salon-orange); }

  .card-art { position: absolute; inset: 0; width: 100%; height: 100%; }

  .brand-name {
    position: absolute; left: 0; right: 0;
    text-align: center;
    font-weight: 400;
    line-height: 1;
  }
  .brand-name .name-line {
    display: block;
    font-family: 'Questrial', sans-serif;
    font-size: 50px;
  }
  .brand-name .salon-line {
    display: block;
    font-family: 'Cinzel', serif;
    font-size: 22px;
    letter-spacing: 1px;
    margin-top: 12px;
  }
  .card-front .brand-name { top: 165px; color: var(--salon-blue); padding-right: 16px; }
  .card-front .salon-line { color: var(--ink); }
  .card-back .brand-name { top: 168px; color: var(--card-white); }

  .contact {
    position: absolute; left: 0; right: 0;
    text-align: center;
    font-family: 'Open Sans', sans-serif;
    font-size: 15px;
    color: var(--ink);
  }
  .card-front .phone { top: 262px; display: flex; justify-content: center; align-items: center; gap: 8px; padding-right: 16px; }
  .card-front .address { top: 303px; padding-right: 16px; }
  .card-back .address { top: 295px; color: var(--card-white); font-weight: 600; }
  .phone-icon { width: 13px; height: 13px; fill: var(--salon-orange); }
</style>
</head>
<body>

<section class="card card-front" aria-label="Business card front">
  <svg class="card-art" viewBox="0 0 588 363" aria-hidden="true">
    <rect class="top-band" x="0" y="25" width="588" height="98" fill="var(--salon-orange)"/>
    <circle class="emblem-circle" cx="292" cy="76" r="70" fill="var(--card-white)"/>
  </svg>
  <h1 class="brand-name">
    <span class="name-line">Gloss N'Wave</span>
    <span class="salon-line">SALON</span>
  </h1>
  <p class="contact phone">
    <svg class="phone-icon" viewBox="0 0 24 24" aria-hidden="true"><path d="M6.6 10.8a15.1 15.1 0 0 0 6.6 6.6l2.2-2.2a1 1 0 0 1 1-.25 11.4 11.4 0 0 0 3.6.57 1 1 0 0 1 1 1V20a1 1 0 0 1-1 1A17 17 0 0 1 3 4a1 1 0 0 1 1-1h3.5a1 1 0 0 1 1 1c0 1.25.2 2.45.57 3.57a1 1 0 0 1-.25 1z"/></svg>
    909 555-2716
  </p>
  <p class="contact address">318 E Maple Hyw #14 Elm Ridge, Ca 91842</p>
</section>

<section class="card card-back" aria-label="Business card back">
  <svg class="card-art" viewBox="0 0 566 350" aria-hidden="true">
    <rect class="top-band" x="0" y="31" width="566" height="96" fill="var(--card-white)"/>
    <circle class="emblem-circle" cx="283" cy="72" r="68" fill="var(--salon-orange)"/>
  </svg>
  <h2 class="brand-name">
    <span class="name-line">Gloss N'Wave</span>
    <span class="salon-line">SALON</span>
  </h2>
  <p class="contact address">318 E Maple Hyw #14 Elm Ridge, Ca 91842</p>
</section>

</body>
</html>
```